flyer/brochure design to deliver to homes (letter box delivery)

Hi I would like something designed to represent my business Hair & Make up, I have a home based salon but offer mobile services for weddings. I really like beachy colours elegant and not to busy. but open to all different designs.

I will be getting these printed up through Korlen press the product specs are:

Document Trim Size
Horizontal
216 x 139 mm
2556 x 1642 pixels
Vertical
139 x 216 mm
1642 x 2556 pixels

Full Bleed Size
Horizontal
219 x 142 mm
2592 x 1677 pixels
Vertical
142 x 219 mm
1677 x 2592 pixels
Finished artwork should use the full bleed dimensions for best results.

I will also upload a recent business card that i have but dont have to stick to similar design

Industry/Entity Type

Salon

Requirements
Must have
• my logo (you can change the colour of my logo if you like)

would like it to have somewhere:
"look good feel great without paying silly prices"

must also have:

private home salon based in bateau bay, mobile service provided for weddings only

Im thinking I would like the price list on the back but open to what ever you submit

price list:
Ladies Cut $20
Ladies Blowdry $20 from
Mens cut $15
Full head of Foils, Toner, Cut & Blowdry $110
Half Head of Foils, Toner, Cut & Blowdry $80
Tint cut & colour $60-80
Tint with scattered foils Cut & Blowdry $70-$110

Wedding Package Hair & Make up $135pp mobile servive provided
check out our webpage for our complete pricelist

prices subject to change without notice

business details:

p: 0482 736 194
E: cts@quorix.com.au
W: www.coraltressstudio.com.au

I would like it to have maybe on the front as an initial eye catcher:

Full head of foils, Toner, Cut & Blowdry $110 every day

```html
<!DOCTYPE html>
<html lang="en">
<head>
<meta charset="utf-8">
<title>Coral Tress Studio – Flyer</title>
<link rel="stylesheet" href="https://fonts.googleapis.com/css2?family=Cinzel:wght@400;700&family=Great+Vibes&display=swap">
<style>
  :root {
    --coral: #e0413f;
    --coral-deep: #d8302f;
    --coral-soft: #f3a3a0;
    --blush: #fbe3e1;
    --white: #ffffff;
    --ink: #2b2b2b;
    --gold: #e38a3a;
    --amber: #c9621f;
    --logo: #ef8a2f;
  }
  * { margin: 0; padding: 0; box-sizing: border-box; }
  html, body { width: 1200px; height: 878px; overflow: hidden; background: #ffffff; }
  body { position: relative; font-family: "Cinzel", serif; }

  /* ---------- Front ---------- */
  .front {
    position: absolute; left: 43px; top: 2px; width: 561px; height: 874px;
    background: var(--white); border: 1px solid #d9d9d9; overflow: hidden;
  }
  .hero-photo {
    position: absolute; left: 0; top: 0; width: 100%; height: 590px;
    background:
      radial-gradient(circle at 62% 28%, #f6d2b4 0%, rgba(246,210,180,0) 28%),
      radial-gradient(circle at 78% 60%, #c8451c 0%, rgba(200,69,28,0) 45%),
      radial-gradient(circle at 15% 75%, #f2b24a 0%, rgba(242,178,74,0) 40%),
      linear-gradient(160deg, #f4c25a 0%, #e0782c 45%, #a9381b 100%);
  }
  .offer-badge {
    position: absolute; left: 82px; top: 24px; width: 166px; height: 166px; border-radius: 50%;
    background: radial-gradient(circle at 40% 35%, #f07a74 0%, var(--coral) 60%, #c9292a 100%);
    color: var(--white); text-align: center;
    display: flex; flex-direction: column; justify-content: center; align-items: center;
    transform: rotate(-22deg); font-weight: 700; line-height: 1.02;
  }
  .offer-badge span { display: block; font-size: 17px; }
  .offer-badge .offer-price { font-size: 25px; }
  .headline {
    position: absolute; left: 28px; top: 360px; color: var(--white);
    font-size: 59px; line-height: 68px; letter-spacing: 0.5px; font-weight: 400;
  }
  .headline b { font-weight: 700; }
  .tagline {
    position: absolute; left: 0; top: 598px; width: 100%; text-align: center;
    color: var(--coral-deep); font-size: 29px; font-weight: 700;
  }
  .salon-note {
    position: absolute; left: 0; top: 638px; width: 100%; text-align: center; color: var(--ink);
  }
  .salon-note .line-main { font-size: 20px; }
  .salon-note .line-sub { font-size: 15px; margin-top: 2px; }
  .contact-band {
    position: absolute; left: 0; top: 697px; width: 100%; height: 81px; text-align: center; color: var(--white);
    background: linear-gradient(90deg, var(--coral) 0%, #f4a6a2 50%, var(--coral) 100%);
  }
  .contact-band .phone { font-size: 45px; line-height: 52px; padding-top: 4px; letter-spacing: 1px; }
  .contact-band .web { font-size: 15px; letter-spacing: 0.5px; }
  .brand-name {
    position: absolute; left: 0; top: 796px; width: 100%; text-align: center;
    color: var(--logo); font-size: 27px; font-weight: 700; line-height: 30px;
  }

  /* ---------- Back ---------- */
  .back {
    position: absolute; left: 636px; top: 0; width: 564px; height: 878px; overflow: hidden;
    background: linear-gradient(90deg, var(--coral) 0%, #f08b86 50%, var(--coral) 100%);
    color: var(--white); text-align: center;
  }
  .back-title {
    position: absolute; left: 0; top: 24px; width: 100%;
    font-size: 70px; line-height: 80px; font-weight: 400; letter-spacing: 1px;
  }
  .price-panel {
    position: absolute; left: 33px; top: 115px; width: 498px; height: 730px; border-radius: 14px;
    background: linear-gradient(90deg, rgba(255,255,255,0.12) 0%, rgba(255,255,255,0.55) 50%, rgba(255,255,255,0.12) 100%);
  }
  .price-item { position: absolute; left: 0; width: 100%; font-size: 17px; line-height: 21px; }
  .price-item .cost { display: block; }
  .wedding-title {
    position: absolute; left: 0; top: 588px; width: 100%;
    font-family: "Great Vibes", cursive; font-size: 36px;
  }
  .small-caps-note { position: absolute; left: 0; width: 100%; font-size: 13px; }
  .web-note { position: absolute; left: 0; top: 731px; width: 100%; font-size: 17px; line-height: 22px; color: var(--ink); }
  .fine-print { top: 799px; color: var(--ink); font-size: 12px; }
</style>
</head>
<body>

<section class="front">
  <div class="hero-photo" role="img" aria-label="Glamour photograph of a woman with long flowing copper-red hair against warm golden bokeh lights"></div>
  <div class="offer-badge">
    <span>Full head</span>
    <span>of foils,</span>
    <span>Toner, Cut</span>
    <span>&amp; Blowdry</span>
    <span class="offer-price">$110</span>
    <span>every day</span>
  </div>
  <h1 class="headline">LOOK<br><b>GOOD</b> AND<br>FEEL <b>GREAT</b></h1>
  <p class="tagline">WITHOUT PAYING SILLY PRICES</p>
  <div class="salon-note">
    <p class="line-main">PRIVATE HOME SALON BASED IN BATEAU BAY</p>
    <p class="line-sub">MOBILE SERVICE IS PROVIDED FOR WEDDINGS ONLY</p>
  </div>
  <div class="contact-band">
    <p class="phone">0482 736 194</p>
    <p class="web">WWW.CORALTRESSSTUDIO.COM.AU</p>
  </div>
  <p class="brand-name">CORAL TRESS<br>STUDIO</p>
</section>

<section class="back">
  <h2 class="back-title">PRICE LIST</h2>
  <div class="price-panel"></div>

  <p class="price-item" style="top:131px">Ladies Cut<span class="cost">$20</span></p>
  <p class="price-item" style="top:195px">Ladies Blowdry<span class="cost">From $20</span></p>
  <p class="price-item" style="top:260px">Mens cut<span class="cost">$15</span></p>
  <p class="price-item" style="top:324px">Full head of Foils, Toner, Cut &amp; Blowdry<span class="cost">$110</span></p>
  <p class="price-item" style="top:389px">Half Head of Foils, Toner, Cut &amp; Blowdry<span class="cost">$80</span></p>
  <p class="price-item" style="top:453px">Tint cut &amp; colour<span class="cost">$60-80</span></p>
  <p class="price-item" style="top:517px">Tint with scattered foils Cut &amp; Blowdry<span class="cost">$70-$110</span></p>

  <p class="wedding-title">Wedding Package</p>
  <p class="price-item" style="top:644px">Hair &amp; Make up<span class="cost">$135pp</span></p>
  <p class="small-caps-note" style="top:692px">MOBILE SERVICE PROVIDED</p>

  <p class="web-note">CHECK OUT OUR WEBPAGE<br>FOR OUR COMPLETE PRICELIST</p>
  <p class="small-caps-note fine-print">PRICES SUBJECT TO CHANGE WITHOUT NOTICE</p>
</section>

</body>
</html>
```